SkyvornQ Business Cards and Stationary Design

Need a design for our business cards and stationary. I want to carry on the theme of the logo. I want the business cards to have a design on the back. I would like the business cards and the stationary to carry the same theme, design scheme, and branding

Target Market(s)

Airlines and Maintenance Facilities

Industry/Entity Type

Aviation

Contact Information for Business Card

Name
Position Title
Address: 4827 Trellis Hollow Road, Brenlow Harbor, Kestria, 34951
Office Number
Mobile Number
Email
Website

Font styles to use
Serif
Sans Serif

Colors

Designer to choose colors to be used in the design.

```html
<!DOCTYPE html>
<html lang="en">
<head>
<meta charset="utf-8">
<title>SkyvornQ Business Card</title>
<link rel="stylesheet" href="https://fonts.googleapis.com/css2?family=Montserrat:wght@400;500;700;800&display=swap">
<style>
  :root {
    --navy: #14295a;
    --navy-deep: #0f2149;
    --sky: #2a9fdb;
    --white: #ffffff;
    --ink-soft: #5b6478;
    --page: #e9ebef;
    --ghost-light: rgba(255,255,255,0.06);
    --ghost-dark: rgba(20,41,90,0.06);
  }
  * { box-sizing: border-box; margin: 0; padding: 0; }
  html, body { width: 1200px; height: 900px; overflow: hidden; }
  body {
    background: var(--page);
    font-family: "Montserrat", sans-serif;
    position: relative;
  }
  .card {
    position: absolute;
    left: 320px;
    width: 560px;
    height: 320px;
    border-radius: 18px;
    overflow: hidden;
    box-shadow: 0 14px 30px rgba(15,33,73,0.22);
  }
  .card-back { top: 100px; background: linear-gradient(135deg, #1a3368, var(--navy-deep)); }
  .card-front { top: 480px; background: var(--white); }

  .ghost-ring { position: absolute; border-radius: 50%; }
  .card-back .ghost-ring {
    width: 300px; height: 300px; left: 250px; top: -40px;
    border: 22px solid var(--ghost-light);
  }
  .card-front .ghost-ring {
    width: 250px; height: 250px; left: 60px; top: 50px;
    border: 18px solid var(--ghost-dark);
  }

  .brand { position: absolute; display: flex; align-items: center; gap: 14px; }
  .brand-dot { width: 38px; height: 38px; border-radius: 50%; border: 4px solid currentColor; }
  .brand-name { font-weight: 800; font-size: 34px; letter-spacing: 6px; }
  .card-back .brand { color: var(--white); left: 50%; top: 50%; transform: translate(-50%, -50%); }
  .card-front .brand { color: var(--navy); left: 36px; top: 150px; }
  .card-front .brand-name { font-size: 28px; letter-spacing: 5px; }
  .card-front .brand-dot { width: 32px; height: 32px; }

  .wave { position: absolute; inset: 0; width: 100%; height: 100%; }

  .holder { position: absolute; right: 36px; top: 30px; text-align: right; color: var(--navy); }
  .holder-name { font-weight: 500; font-size: 19px; letter-spacing: 1px; }
  .holder-title { font-size: 11px; color: var(--ink-soft); margin-top: 2px; }

  .contact {
    position: absolute; right: 26px; top: 170px;
    list-style: none; color: var(--white);
    font-size: 11px; line-height: 17px; text-align: right;
  }
  .contact li { display: flex; justify-content: flex-end; align-items: center; gap: 6px; }
  .contact .icon { width: 10px; height: 10px; flex: none; }
  .contact .spacer { width: 10px; flex: none; }
  .contact strong { font-weight: 700; }
</style>
</head>
<body>

  <section class="card card-back" aria-label="Business card back">
    <div class="ghost-ring"></div>
    <div class="brand">
      <span class="brand-dot"></span>
      <span class="brand-name">SKYVORNQ</span>
    </div>
  </section>

  <section class="card card-front" aria-label="Business card front">
    <div class="ghost-ring"></div>

    <svg class="wave" viewBox="0 0 560 320" preserveAspectRatio="none" aria-hidden="true">
      <path d="M560,58 C466,64 418,120 388,186 C358,252 298,284 200,294 L560,294 Z" fill="var(--navy)"/>
      <path d="M560,42 C452,48 402,108 372,176 C342,244 282,274 170,286" fill="none" stroke="var(--navy)" stroke-width="5"/>
      <path d="M0,288 C140,300 290,290 372,228 C322,282 170,312 0,306 Z" fill="var(--sky)"/>
      <path d="M0,313 C200,318 380,300 560,268 L560,320 L0,320 Z" fill="var(--navy)"/>
    </svg>

    <div class="brand">
      <span class="brand-dot"></span>
      <span class="brand-name">SKYVORNQ</span>
    </div>

    <div class="holder">
      <p class="holder-name">DANIEL HARWOOD</p>
      <p class="holder-title">Director</p>
    </div>

    <ul class="contact">
      <li>772-318-5906
        <svg class="icon" viewBox="0 0 10 10"><path d="M2 0.5 L4 2.8 L3 4 Q4.5 6 6 7 L7.2 6 L9.5 8 L8.3 9.5 Q3 8.5 0.5 1.7 Z" fill="var(--white)"/></svg>
      </li>
      <li>info@skyvornq.com
        <svg class="icon" viewBox="0 0 10 10"><rect x="0.7" y="2" width="8.6" height="6" fill="none" stroke="var(--white)"/><path d="M0.7 2 L5 5.5 L9.3 2" fill="none" stroke="var(--white)"/></svg>
      </li>
      <li><span>www.<strong>skyvornq</strong>.com</span>
        <svg class="icon" viewBox="0 0 10 10"><circle cx="5" cy="5" r="4.2" fill="none" stroke="var(--white)"/><path d="M1 5 H9 M5 0.8 Q2.5 5 5 9.2 Q7.5 5 5 0.8" fill="none" stroke="var(--white)" stroke-width="0.8"/></svg>
      </li>
      <li>4827 Trellis Hollow Road,<span class="spacer"></span></li>
      <li>Brenlow Harbor, Kestria, 34951<span class="spacer"></span></li>
    </ul>
  </section>

</body>
</html>
```